Business Card for brovaLINK

Create a Business Card with an existing logo for brovaLINK AG. We are a Information Technology company that does consulting and developing SW to automate business processes. The main colors are given from the logo.

Industry/Entity Type

Business

Requirements
Nice to have
• we use a a font style Century Gothic in our documents

```html
<!DOCTYPE html>
<html lang="en">
<head>
<meta charset="utf-8">
<title>brovaLINK AG – Business Card</title>
<link href="https://fonts.googleapis.com/css2?family=Questrial&family=Mulish:wght@400;700;800&display=swap" rel="stylesheet">
<style>
  :root {
    --page: #e9eaec;
    --card: #ffffff;
    --card-grey: #eceef0;
    --ink: #3a3a3c;
    --ink-soft: #55575a;
    --blue: #1f6fc0;
    --blue-light: #3fa3e0;
    --green: #39a935;
    --green-light: #9fd62f;
  }
  * { margin: 0; padding: 0; box-sizing: border-box; }
  html, body { width: 1200px; height: 1024px; overflow: hidden; }
  body {
    background: var(--page);
    font-family: "Mulish", sans-serif;
    color: var(--ink);
    position: relative;
  }
  .card {
    position: absolute;
    left: 220px;
    width: 760px;
    height: 434px;
    border-radius: 26px;
    overflow: hidden;
    background: var(--card);
    box-shadow: 0 10px 28px rgba(0,0,0,.14);
  }
  .card--front { top: 48px; }
  .card--back { top: 542px; background: linear-gradient(135deg, #f7f8f9, var(--card-grey)); }
  .card__art { position: absolute; inset: 0; width: 100%; height: 100%; }

  .brand {
    position: absolute;
    display: flex;
    align-items: center;
    gap: 16px;
  }
  .brand__dot {
    width: 46px; height: 46px; border-radius: 50%;
    background: var(--blue);
  }
  .brand__name {
    font-family: "Questrial", sans-serif;
    font-size: 62px;
    color: var(--ink);
    letter-spacing: -1px;
  }
  .card--front .brand { left: 58px; top: 176px; }
  .card--back .brand { left: 250px; top: 150px; }

  .contact { position: absolute; left: 420px; top: 52px; }
  .contact__name { font-weight: 800; font-size: 26px; color: var(--blue); }
  .contact__role { font-weight: 700; font-size: 17px; color: var(--green); margin-top: 2px; }
  .contact__list { list-style: none; margin-top: 22px; }
  .contact__item {
    display: flex; align-items: center; gap: 10px;
    font-size: 17px; color: var(--ink-soft); line-height: 28px;
  }
  .contact__icon { width: 16px; height: 16px; flex: none; }

  .url { position: absolute; font-family: "Questrial", sans-serif; font-size: 19px; }
  .card--front .url { right: 40px; bottom: 118px; color: #fff; }
  .card--back .url { left: 44px; bottom: 60px; color: var(--ink-soft); }
  .url__accent { color: var(--green); }
</style>
</head>
<body>

<section class="card card--front" aria-label="Business card front">
  <svg class="card__art" viewBox="0 0 760 434" preserveAspectRatio="none" aria-hidden="true">
    <defs>
      <linearGradient id="bandBlue" x1="0" y1="0" x2="1" y2="0">
        <stop offset="0" stop-color="#1f6fc0"/>
        <stop offset="1" stop-color="#3fa3e0"/>
      </linearGradient>
    </defs>
    <line x1="400" y1="30" x2="400" y2="180" stroke="#e4e6e8" stroke-width="1.5"/>
    <path d="M0 434 L0 420 L470 420 L540 300 L760 300 L760 434 Z" fill="url(#bandBlue)"/>
    <path d="M0 412 L466 412 L536 292 L760 292 L760 300 L540 300 L470 420 L0 420 Z" fill="#39a935"/>
  </svg>

  <div class="brand">
    <span class="brand__dot"></span>
    <span class="brand__name">brovaLINK</span>
  </div>

  <div class="contact">
    <p class="contact__name">Lukas Brenner</p>
    <p class="contact__role">CEO</p>
    <ul class="contact__list">
      <li class="contact__item">
        <svg class="contact__icon" viewBox="0 0 16 16"><circle cx="8" cy="8" r="8" fill="#39a935"/><path d="M5 4.5h2l.6 2-1 .8a5 5 0 0 0 2.1 2.1l.8-1 2 .6v2c-3.5.3-6.8-3-6.5-6.5z" fill="#fff"/></svg>
        +41 56 210 48 90
      </li>
      <li class="contact__item">
        <svg class="contact__icon" viewBox="0 0 16 16"><circle cx="8" cy="8" r="8" fill="#39a935"/><rect x="5.5" y="3.5" width="5" height="9" rx="1" fill="#fff"/></svg>
        +41 79 436 27 15
      </li>
      <li class="contact__item">
        <svg class="contact__icon" viewBox="0 0 16 16"><circle cx="8" cy="8" r="8" fill="#39a935"/><circle cx="8" cy="8" r="4" fill="none" stroke="#fff" stroke-width="1.2"/><line x1="4" y1="8" x2="12" y2="8" stroke="#fff" stroke-width="1.2"/></svg>
        www.brovalink.ch
      </li>
      <li class="contact__item">
        <svg class="contact__icon" viewBox="0 0 16 16"><circle cx="8" cy="8" r="8" fill="#39a935"/><rect x="4" y="5" width="8" height="6" fill="#fff"/><path d="M4 5l4 3 4-3" fill="none" stroke="#39a935" stroke-width="1"/></svg>
        lukas.brenner@brovalink.ch
      </li>
    </ul>
  </div>

  <p class="url">www.brovalink.ch</p>
</section>

<section class="card card--back" aria-label="Business card back">
  <svg class="card__art" viewBox="0 0 760 434" preserveAspectRatio="none" aria-hidden="true">
    <defs>
      <linearGradient id="waveBlue" x1="0" y1="0" x2="1" y2="1">
        <stop offset="0" stop-color="#3fa3e0"/>
        <stop offset="1" stop-color="#b9d9f2"/>
      </linearGradient>
      <linearGradient id="waveGreen" x1="0" y1="0" x2="1" y2="1">
        <stop offset="0" stop-color="#c8ec4a"/>
        <stop offset="1" stop-color="#39a935"/>
      </linearGradient>
    </defs>
    <path d="M0 0 L210 0 C160 50 150 110 90 130 C50 142 20 150 0 170 Z" fill="url(#waveBlue)"/>
    <path d="M760 170 C640 190 560 230 500 330 C470 380 440 410 410 434 L760 434 Z" fill="#39a935"/>
    <path d="M760 186 C650 206 578 244 520 340 C492 386 466 412 440 434 L760 434 Z" fill="url(#waveGreen)"/>
  </svg>

  <div class="brand">
    <span class="brand__dot"></span>
    <span class="brand__name">brovaLINK</span>
  </div>

  <p class="url">www.<span class="url__accent">brovalink</span>.ch</p>
</section>

</body>
</html>
```